Business Cards for IT Consulting Company (Managed Service Provider)

I am looking to have some business cards printed and would like some designs. We are an IT Consulting company based in Vancouver BC. I would like a nice clean and modern look to the cards. I have uploaded all the versions of my logo so parts can be used as needed. Here is a snippit from our website homepage:

Quillbrook Networks Ltd. is an IT Solutions Partner located in Vancouver BC, Canada. We offer IT solutions and support to customers in the greater Vancouver Area. With expertise in Microsoft platforms, as well as Linux and Mac OSX and over 12 years experience in the IT industry, Quillbrook Networks is dedicated to offering our clients top quality service and products. We take pride in the solutions we offer our customers. The greatest compliment a client can give us is to recommend our services.

Quillbrook Networks Ltd. offers a wide range of IT services from onsite service to remote support and managed service solutions. This allows clients to choose the support path that best suits their company’s needs. Supporting many different sized companies from small to enterprise level over the past 12 years Quillbrook Networks has the experience and expertise needed to ensure things run smoothly. Allowing our clients to focus on doing business.

Revolutionizing the way IT services are delivered.

Quillbrook Networks is dedicated to providing our clients with IT solutions that work and grow with them for years to come. This philosophy helps save money in the long run instead of replacing equipment constantly. Far too often IT solutions are not well thought out and while possibly solving the problem at hand, require replacement due to growth or quality within a very short time frame. Quillbrook Networks takes pride in providing solutions that will last and be able to accommodate growth without the need for replacement.

Industry/Entity Type

Information Technology

Contact Information for Business Card

Quillbrook Networks Ltd.
(Employee Name)
Eml: (Employees Email Address)
Web: quillbrook.me
Ph: 604-555-0148

Font styles to use
Serif
Sans Serif

Requirements
Must have
• The Company logo and company colors.
Nice to have
• - Our tag line: "Revolutionizing IT Services" or "Revolutionizing the way IT services are delivered."
• - Also I really like the idea of nature and technology together blending which is sort of where my logo came from so integrating that somehow onto the business cards would be great.

```html
<!DOCTYPE html>
<html lang="en">
<head>
<meta charset="utf-8">
<title>Quillbrook Networks Ltd. – Business Cards</title>
<link href="https://fonts.googleapis.com/css2?family=Montserrat:wght@600&family=Lato:wght@400;700&display=swap" rel="stylesheet">
<style>
  :root {
    --backdrop: #2b2b2d;
    --card: #f7f7f7;
    --brand-blue: #2a9fd8;
    --ink: #4a4a4c;
    --ink-soft: #77777a;
  }
  * { box-sizing: border-box; margin: 0; padding: 0; }
  html, body {
    width: 1200px; height: 997px; overflow: hidden;
    background: var(--backdrop);
    font-family: "Lato", sans-serif;
  }
  .stage { position: relative; width: 1200px; height: 997px; }
  .card {
    position: absolute;
    width: 540px; height: 309px;
    background: var(--card);
    box-shadow: 0 12px 30px rgba(0,0,0,.45);
  }
  .card--front { left: 70px; top: 170px; }
  .card--back  { left: 590px; top: 500px; }

  .brand { display: flex; align-items: center; gap: 12px; }
  .brand__mark {
    width: 30px; height: 30px;
    border: 3px solid var(--brand-blue);
    flex: none;
  }
  .brand__name {
    font-family: "Montserrat", sans-serif;
    font-weight: 600;
    color: var(--brand-blue);
    font-size: 22px;
    letter-spacing: .2px;
  }

  .card--front .brand { position: absolute; left: 36px; top: 40px; }
  .web {
    position: absolute; right: 34px; top: 44px;
    display: flex; align-items: center; gap: 8px;
    font-size: 12px; color: var(--ink-soft);
  }
  .web svg { width: 12px; height: 12px; }
  .person { position: absolute; left: 36px; top: 128px; }
  .person__name { font-size: 20px; font-weight: 700; color: var(--brand-blue); }
  .person__role { font-size: 12px; color: var(--ink-soft); margin-top: 2px; }
  .contacts {
    position: absolute; left: 36px; bottom: 34px;
    list-style: none; display: grid; gap: 10px;
    font-size: 13px; color: var(--ink-soft);
  }
  .contacts li { display: flex; align-items: center; gap: 12px; }
  .contacts svg { width: 13px; height: 13px; flex: none; }

  .card--back { display: flex; align-items: center; justify-content: center; }
  .card--back .brand__mark { width: 44px; height: 44px; border-width: 4px; }
  .card--back .brand__name { font-size: 30px; }
  .tagline {
    font-size: 14px; font-weight: 700; letter-spacing: 2.5px;
    color: var(--ink); margin-top: 8px; padding-left: 58px;
  }
</style>
</head>
<body>
<main class="stage">
  <section class="card card--front" aria-label="Business card front">
    <div class="brand">
      <span class="brand__mark"></span>
      <span class="brand__name">Quillbrook Networks Ltd.</span>
    </div>
    <div class="web">
      <span>www.quillbrook.me</span>
      <svg viewBox="0 0 12 12" aria-hidden="true"><circle cx="6" cy="6" r="5" fill="none" stroke="#2a9fd8" stroke-width="1.4"/><path d="M1 6h10M6 1c2 2 2 8 0 10M6 1c-2 2-2 8 0 10" fill="none" stroke="#2a9fd8" stroke-width="1"/></svg>
    </div>
    <div class="person">
      <p class="person__name">Daniel Marsh</p>
      <p class="person__role">Network Engineer</p>
    </div>
    <ul class="contacts">
      <li>
        <svg viewBox="0 0 13 13" aria-hidden="true"><rect x="3" y="1" width="7" height="11" rx="1.5" fill="none" stroke="#2a9fd8" stroke-width="1.3"/></svg>
        <span>604-555-0148</span>
      </li>
      <li>
        <svg viewBox="0 0 13 13" aria-hidden="true"><rect x="1" y="3" width="11" height="8" fill="#2a9fd8"/><path d="M1 3l5.5 4.5L12 3" fill="none" stroke="#f7f7f7" stroke-width="1"/></svg>
        <span>dmarsh@quillbrook.me</span>
      </li>
    </ul>
  </section>

  <section class="card card--back" aria-label="Business card back">
    <div>
      <div class="brand">
        <span class="brand__mark"></span>
        <span class="brand__name">Quillbrook Networks Ltd.</span>
      </div>
      <p class="tagline">Revolutionizing IT Services</p>
    </div>
  </section>
</main>
</body>
</html>
```